Veltrane Group Business Card Design

The CEO is looking for a new trendy look for his business card.
You can stay with current branding or come up with something new/creative. It can be 3D, including Medical Office buildings. You can use our logo in a variety of colors. Please include name, title, company name, company website, email address, cell number

Target Market(s)

Real Estate Development and Construction

Industry/Entity Type

Health care real estate

Contact Information for Business Card

Rohesh Kamdar, CEO M-604.781.2249 E-roheshkamdar@veltrane.com Address:4180 Lindqvist Ave, Tampa, FL 33482 www.veltrane.com

Font styles to use
Other font styles liked:
• Be creative

Requirements
Must have
• Creative, trendy look
Nice to have
• Please go to our website to get a feel- www. veltrane.com
Should not have
• small fonts

```html
<!DOCTYPE html>
<html lang="en">
<head>
<meta charset="utf-8">
<title>Veltrane Group Business Card</title>
<link href="https://fonts.googleapis.com/css2?family=Libre+Franklin:wght@400;600;800&display=swap" rel="stylesheet">
<style>
  :root {
    --brand-red: #b01f2a;
    --brand-navy: #1c2b4a;
    --card-white: #ffffff;
    --ink: #333a44;
    --divider: #c9ccd1;
    --backdrop: #2a2b2e;
  }
  * { box-sizing: border-box; margin: 0; padding: 0; }
  html, body {
    width: 1200px; height: 874px; overflow: hidden;
    background: var(--backdrop);
    font-family: "Libre Franklin", Arial, sans-serif;
  }
  .stage { position: relative; width: 1200px; height: 874px; }
  .card {
    position: absolute; left: 320px; width: 560px; height: 320px;
    border-radius: 22px; overflow: hidden;
    box-shadow: 0 14px 30px rgba(0,0,0,0.45);
  }
  .card-front { top: 78px; background: var(--brand-red); }
  .card-back { top: 476px; background: var(--card-white); }

  .company-name {
    font-weight: 800; line-height: 1; white-space: nowrap;
  }
  .card-front .company-name {
    position: absolute; left: 0; right: 0; top: 130px;
    text-align: center; color: var(--card-white); font-size: 54px;
  }
  .card-back .company-name {
    position: absolute; left: 30px; top: 136px; width: 250px;
    color: var(--brand-red); font-size: 28px;
  }

  .divider {
    position: absolute; left: 292px; top: 70px; width: 1px; height: 160px;
    background: var(--divider);
  }
  .contact {
    position: absolute; left: 312px; top: 70px; width: 236px; color: var(--ink);
  }
  .contact .name { color: var(--brand-red); font-weight: 600; font-size: 21px; }
  .contact .title { font-size: 12px; color: var(--brand-navy); margin-bottom: 16px; }
  .contact .address { font-size: 13px; line-height: 1.35; margin-bottom: 14px; }
  .contact ul { list-style: none; font-size: 13px; line-height: 1.45; }
  .contact li { display: flex; align-items: center; gap: 7px; white-space: nowrap; }
  .contact svg { width: 11px; height: 11px; flex: none; fill: var(--brand-red); }

  .base-band {
    position: absolute; left: 0; right: 0; bottom: 0; height: 36px;
    background: var(--brand-red);
    border-top: 3px solid var(--card-white);
    box-shadow: 0 -3px 0 var(--brand-navy);
  }
</style>
</head>
<body>
<main class="stage">
  <section class="card card-front" aria-label="Card front">
    <p class="company-name">Veltrane Group</p>
  </section>

  <section class="card card-back" aria-label="Card back">
    <p class="company-name">Veltrane Group</p>
    <div class="divider"></div>
    <div class="contact">
      <p class="name">Rohesh Kamdar</p>
      <p class="title">CEO</p>
      <p class="address">4180 Lindqvist Ave, Tampa<br>FL 33482</p>
      <ul>
        <li><svg viewBox="0 0 24 24"><path d="M6.6 10.8a15.1 15.1 0 0 0 6.6 6.6l2.2-2.2c.3-.3.7-.4 1-.2 1.1.4 2.3.6 3.6.6.6 0 1 .4 1 1V20c0 .6-.4 1-1 1A17 17 0 0 1 3 4c0-.6.4-1 1-1h3.5c.6 0 1 .4 1 1 0 1.3.2 2.5.6 3.6.1.3 0 .7-.2 1z"/></svg>604.781.2249</li>
        <li><svg viewBox="0 0 24 24"><path d="M2 5h20v14H2z M2 5l10 8 10-8" fill="none" stroke="#b01f2a" stroke-width="2.5"/></svg>roheshkamdar@veltrane.com</li>
        <li><svg viewBox="0 0 24 24"><circle cx="12" cy="12" r="10"/></svg>www.veltrane.com</li>
      </ul>
    </div>
    <div class="base-band"></div>
  </section>
</main>
</body>
</html>
```